Design and Renovation Company Luxury Business Card

I want to create a luxury business card for a Design and Renovation Firm . We will use our current logo. The company name is 528BUILDA. We do not want anything standard. We need a very unique concept.
Please see uploaded inspiration. I really like the textured paper option. I would like the card to be thick with debossing, and/or embossing options. The logo has orange in it but I would like to see the card with and without the orange. I think the orange may make the company feel less high-end. The goal is to elevate the logo not match its vibe per se of the logo. We want something very unique, not standard at all!
I would like a space for :
Logo,
Name,
Position,
Email,
Office number,
Website Address,
Business Address,
Thank you!
Have fun!
Target Market(s)
Home owners Age 35 +
Industry/Entity Type
Design and Renovation
Contact Information for Business Card
Logo, Name, Position, Email, Office number, Website Address, Business Address,.
Colors
Designer to choose colors to be used in the design.
Requirements
Must have
- A luxury designer feel. Must be black or dark grey but open to other luxury ideas.
Nice to have
- Gold, silver, black embossing or debossing. Textured paper design.
Should not have
- A cheap look and feel.

```html
<!DOCTYPE html>
<html lang="en">
<head>
<meta charset="utf-8">
<title>528BUILDA Business Card</title>
<link rel="stylesheet" href="https://fonts.googleapis.com/css2?family=Poppins:wght@300;400;500;600&display=swap">
<style>
  :root {
    --page-bg: #e3e7e8;
    --card-bg: #212125;
    --accent: #f3921f;
    --ink-light: #ffffff;
    --ink-deep: #0e0e10;
  }
  * { margin: 0; padding: 0; box-sizing: border-box; }
  html, body {
    width: 1200px;
    height: 960px;
    overflow: hidden;
    background: var(--page-bg);
    font-family: "Poppins", sans-serif;
  }
  .card {
    position: absolute;
    left: 250px;
    width: 702px;
    height: 400px;
    background: var(--card-bg);
    border-bottom: 2px solid var(--accent);
  }
  .card--front { top: 60px; }
  .card--back { top: 500px; }

  .brand-name {
    position: absolute;
    left: 0;
    right: 0;
    top: 160px;
    text-align: center;
    font-weight: 600;
    font-size: 58px;
    line-height: 1;
    letter-spacing: 2px;
    color: var(--ink-deep);
  }

  .contact {
    position: absolute;
    left: 0;
    right: 0;
    top: 127px;
    text-align: center;
    color: var(--ink-light);
  }
  .contact__name {
    font-size: 54px;
    line-height: 1;
    letter-spacing: 0.5px;
    font-weight: 400;
  }
  .contact__first { font-weight: 600; color: var(--accent); }
  .contact__last { font-weight: 300; }
  .contact__role {
    margin-top: 4px;
    font-weight: 500;
    font-size: 19px;
    line-height: 1.2;
  }
  .contact__details {
    margin-top: 40px;
    font-weight: 400;
    font-size: 20px;
    line-height: 26px;
  }
  .contact__address {
    margin-top: 4px;
    font-size: 19.5px;
    line-height: 26px;
    color: var(--accent);
  }
</style>
</head>
<body>
  <section class="card card--front">
    <p class="brand-name">528BUILDA</p>
  </section>

  <section class="card card--back">
    <div class="contact">
      <h1 class="contact__name"><span class="contact__first">Marta</span> <span class="contact__last">Koval</span></h1>
      <p class="contact__role">Founder &amp; CEO</p>
      <p class="contact__details">
        (555) 214-3086<br>
        info@yourwebsite.com<br>
        www.yourwebsite.com
      </p>
      <p class="contact__address">1840 Maple Crest Dr. Suite 210 Arlington, TX 76010</p>
    </div>
  </section>
</body>
</html>
```